Satchel & Sundial needs new business card design

I need a new business card design. I'm looking for out-of-the-box design which represents the freedom of being a location independent entrepreneur.
I offer coaching, retreats and trips.
I would like to see designs with and without the photo.
Colors I use are black (#000000), green (#25A796) and brown (#D7C38C)
Website satchelandsundial.example

Target Market(s)

location independent entrepreneurs, digital nomads, people looking to swap the 9 to 5 for a lifestyle business

Industry/Entity Type

Business

Contact Information for Business Card

Dorota Falkner
Your Lifestyle Business Coach, Retreat & Trip Leader
http://satchelandsundial.example
hello@satchelandsundial.example
Live a life you don't need a holiday from

Font styles to use
Serif
Sans Serif

Requirements
Must have
• One side should contain only the logo. I would also consider having the "Live a life you don't need a holiday from" on that side too (depending on how it looks)
• Please show both sides on the designs.

```html
<!DOCTYPE html>
<html lang="en">
<head>
<meta charset="utf-8">
<title>Satchel & Sundial — Business Card</title>
<link rel="stylesheet" href="https://fonts.googleapis.com/css2?family=Questrial&display=swap">
<style>
  :root {
    --ink: #1e1e1e;
    --green: #25A796;
    --green-deep: #1f9c8c;
    --paper: #ffffff;
    --backdrop: #ece8df;
    --muted: #3a3a3a;
    --rule: #c9c9c9;
  }
  * { box-sizing: border-box; margin: 0; padding: 0; }
  html, body { width: 1200px; height: 1023px; overflow: hidden; }
  body {
    background: var(--backdrop);
    font-family: "Questrial", "Century Gothic", sans-serif;
    color: var(--ink);
    display: flex;
    flex-direction: column;
    align-items: center;
    justify-content: center;
    gap: 56px;
  }
  .card {
    width: 770px;
    height: 440px;
    border-radius: 4px;
    box-shadow: 0 6px 22px rgba(0,0,0,.18);
    position: relative;
    overflow: hidden;
  }
  /* front side */
  .card--front {
    background: linear-gradient(180deg, #ffffff 0%, #f3f3f3 100%);
    display: grid;
    grid-template-columns: 1fr 1px 1fr;
    align-items: center;
  }
  .front__brand {
    display: flex;
    justify-content: center;
    align-items: center;
    height: 100%;
  }
  .brand-name {
    font-size: 38px;
    letter-spacing: 1px;
    text-transform: uppercase;
    color: var(--ink);
  }
  .front__divider { width: 1px; height: 100%; background: var(--rule); }
  .front__details { padding: 0 40px 0 44px; }
  .person-name { color: var(--green); font-size: 27px; margin-bottom: 6px; }
  .person-role { font-size: 17px; line-height: 1.35; color: var(--muted); margin-bottom: 22px; }
  .contact-list { list-style: none; margin-bottom: 24px; }
  .contact-list li {
    display: flex; align-items: center; gap: 10px;
    font-size: 16px; line-height: 1.7; color: var(--muted);
  }
  .contact-list svg { width: 15px; height: 15px; flex: none; fill: var(--green); }
  .address { font-size: 17px; line-height: 1.35; color: var(--muted); }
  /* back side */
  .card--back {
    background: var(--green);
    display: flex;
    flex-direction: column;
    align-items: center;
    justify-content: center;
  }
  .card--back .brand-name { color: #ffffff; font-size: 56px; }
  .tagline {
    position: absolute;
    bottom: 34px;
    left: 0; right: 0;
    text-align: center;
    color: #e8f7f4;
    font-size: 16px;
    letter-spacing: .4px;
  }
</style>
</head>
<body>

<section class="card card--front" aria-label="Business card front">
  <div class="front__brand">
    <span class="brand-name">Satchel &amp; Sundial</span>
  </div>
  <div class="front__divider"></div>
  <div class="front__details">
    <h1 class="person-name">Dorota Falkner</h1>
    <p class="person-role">Your Lifestyle Business Coach,<br>Retreat &amp; Trip Leader</p>
    <ul class="contact-list">
      <li>
        <svg viewBox="0 0 16 16" aria-hidden="true"><path d="M3.5 1.5l2.5 0 1 3.5-1.8 1.2a8 8 0 0 0 4.6 4.6L11 9l3.5 1v2.5A2 2 0 0 1 12.5 14.5 11 11 0 0 1 1.5 3.5 2 2 0 0 1 3.5 1.5z"/></svg>
        +987 20 31 46 5
      </li>
      <li>
        <svg viewBox="0 0 16 16" aria-hidden="true"><path d="M1 3h14v10H1z M1.8 3.6L8 8.6l6.2-5" fill="none" stroke="#25A796" stroke-width="1.6"/></svg>
        hello@satchelandsundial.example
      </li>
      <li>
        <svg viewBox="0 0 16 16" aria-hidden="true"><circle cx="8" cy="8" r="6.6" fill="none" stroke="#25A796" stroke-width="1.5"/><path d="M1.5 8h13M8 1.4c-3 3.5-3 9.7 0 13.2M8 1.4c3 3.5 3 9.7 0 13.2" fill="none" stroke="#25A796" stroke-width="1.2"/></svg>
        www.satchelandsundial.example
      </li>
    </ul>
    <p class="address">Here your company or<br>home address</p>
  </div>
</section>

<section class="card card--back" aria-label="Business card back">
  <span class="brand-name">Satchel &amp; Sundial</span>
  <p class="tagline">Live a life you don't need a holiday from</p>
</section>

</body>
</html>
```